Upland Bird Hunting Preserve and Pointing Dog kennel

Need Price packages outlined for the bird hunting business. List the kennel and that we provide training and dogs for sale.
The preserve is "Tall Heron Provisions" the dog kennel is "Pine Hollow Setters"
1/2 Day Upland Field Hunts: 5 Pheasants $120
7 Chukar $125
Continental Hunt 12 Pheasants $325 includes meal, minimum 12 hunters
Guides available $100

Target Market(s)

upland bird hunters

Industry/Entity Type

hunting, outdoor

Colors
EE7325
F08F49
F5BC92
FAE3D3
FDF4ED

```html
<!DOCTYPE html>
<html lang="en">
<head>
<meta charset="utf-8">
<title>Tall Heron Provisions – Licensed Shooting Preserve</title>
<link href="https://fonts.googleapis.com/css2?family=Plus+Jakarta+Sans:wght@400;500;600;700;800&display=swap" rel="stylesheet">
<style>
  :root{
    --backdrop:#efd6d1;
    --paper:#ffffff;
    --ink:#111111;
    --orange:#e1532a;
    --red:#c8102e;
    --blush:#fae3d3;
    --grey-box:#ececec;
    --photo-field:#8a7358;
    --photo-woods:#a48a6a;
    --sketch:#d9d9d9;
  }
  *{box-sizing:border-box;margin:0;padding:0}
  html,body{width:1200px;height:2167px;overflow:hidden}
  body{background:var(--backdrop);font-family:"Plus Jakarta Sans",Arial,sans-serif;color:var(--ink);position:relative}
  .flyer{position:absolute;left:49px;top:370px;width:1102px;height:1427px;background:var(--paper);box-shadow:0 6px 24px rgba(0,0,0,.12)}
  .flyer > *{position:absolute}
  .sketch{left:72px;top:66px;width:193px;height:242px;background:linear-gradient(160deg,#f4f4f4,var(--sketch));border-radius:6px}
  .brand-name{left:324px;top:62px;font-size:67px;font-weight:800;line-height:60px;letter-spacing:-.5px}
  .location{left:324px;top:200px;font-size:37px;font-weight:600;display:flex;align-items:center;gap:10px}
  .location svg{width:26px;height:40px}
  .preserve-band{left:322px;top:256px;width:715px;height:57px;background:var(--orange);color:#fff;border-radius:4px;font-size:33px;font-weight:700;padding-left:20px;display:flex;align-items:center}
  .photo{border-radius:12px}
  .photo-group{left:66px;top:330px;width:971px;height:299px;background:linear-gradient(180deg,var(--photo-woods) 0%,#6f5a44 55%,#8b6a4b 100%)}
  .photo-truck{left:583px;top:656px;width:454px;height:290px;background:linear-gradient(180deg,#9a8769 0%,#6c5a46 60%,#3c3530 100%)}
  .photo-chukar{left:921px;top:1246px;width:117px;height:115px;border-radius:4px;background:linear-gradient(160deg,#7d8a5f,#a39a84)}
  .packages{left:66px;top:656px;width:453px;height:290px;border:2px solid var(--ink);border-radius:10px;padding:28px 36px}
  .packages h2{font-size:29px;font-weight:700;line-height:36px;margin-bottom:6px}
  .price-row{display:flex;align-items:baseline;font-size:26px;line-height:33px}
  .price-row .leader{flex:1;border-bottom:1.5px solid var(--ink);margin:0 14px;transform:translateY(-8px)}
  .guide-pill{margin-top:14px;background:var(--blush);border-radius:4px;font-size:17px;font-weight:600;padding:10px 15px;white-space:nowrap}
  .offer h3{font-size:26px;font-weight:700;line-height:32px}
  .offer p{font-size:25px;line-height:33px}
  .continental{left:66px;top:980px;width:460px}
  .continental .gap{margin-top:10px}
  .note{left:66px;top:1146px;width:453px;height:88px;background:var(--grey-box);border-radius:6px;padding:16px 20px;font-size:23px;line-height:29px}
  .guided{left:586px;top:980px;width:460px}
  .guided h3{color:var(--red);font-weight:800}
  .guided .deer{margin-top:12px}
  .contact{left:66px;top:1296px;font-size:29px;font-weight:700;line-height:36px}
  .divider{left:298px;top:1288px;width:3px;height:70px;background:var(--red)}
  .puppies{left:322px;top:1302px;font-size:29px;font-weight:600;line-height:33px}
  .kennel{left:660px;top:1278px;width:220px;height:80px;display:flex;align-items:center;gap:10px;font-size:20px;font-weight:600}
  .kennel .dot{width:14px;height:14px;border-radius:50%;background:var(--ink);flex:none}
</style>
</head>
<body>
  <main class="flyer">
    <div class="sketch" role="img" aria-label="Pen sketch of a hunter with pheasants flushing from tall grass"></div>

    <h1 class="brand-name">TALL HERON<br>PROVISIONS, LLC</h1>
    <div class="location">
      <svg viewBox="0 0 26 40" aria-hidden="true"><circle cx="13" cy="12" r="11" fill="var(--red)"/><rect x="11.5" y="20" width="3" height="20" fill="#777"/></svg>
      <span>CEDAR BEND, MO</span>
    </div>
    <div class="preserve-band">LICENSED SHOOTING PRESERVE</div>

    <div class="photo photo-group" role="img" aria-label="Group of hunters standing in winter woods behind a long row of harvested pheasants"></div>

    <section class="packages">
      <h2>Hunting Packages –<br>½ Day Hunts</h2>
      <div class="price-row"><span>5 Pheasants</span><span class="leader"></span><span>$120</span></div>
      <div class="price-row"><span>7 Chukar</span><span class="leader"></span><span>$125</span></div>
      <div class="price-row"><span>8 Quail</span><span class="leader"></span><span>$100</span></div>
      <div class="guide-pill">GUIDE AVAILABLE $100 PER HALF DAY</div>
    </section>

    <div class="photo photo-truck" role="img" aria-label="Hunters in blaze orange with a white pointing dog on a truck tailgate holding birds"></div>

    <section class="offer continental">
      <h3>Continental Pheasant Hunt</h3>
      <p>12 Hunter Minimum</p>
      <p class="gap">$325 per hunter, includes<br>12 birds per hunter &amp; meal.</p>
    </section>
    <div class="note">All hunts include bird cleaning<br>Lodging available, call for pricing</div>

    <section class="offer guided">
      <h3>Guided Spring Turkey Hunts</h3>
      <p>3 Day Hunt includes meals<br>&amp; lodging – $1600</p>
      <h3 class="deer">Guided Whitetail Deer Hunts<br>– Rifle &amp; Archery</h3>
      <p>5 Day Hunt includes meals<br>&amp; lodging – $2750</p>
    </section>

    <div class="contact">Dale Mercer<br>555-014-2290</div>
    <div class="divider"></div>
    <div class="puppies">Puppies and started<br>dogs available!</div>

    <div class="kennel"><span class="dot"></span><span>Pine Hollow Setters<br>Ashford Falls, MO</span></div>
    <div class="photo-chukar" role="img" aria-label="Chukar partridge standing in grass"></div>
  </main>
</body>
</html>
```